TEBSIRK HOA Portal Site for Public

Clean up and organize current website; need website to look good and functional; this is a HOA (homeowner association management) website where homeowners can login and pay their bill, general information about a HOA, monthly newsletter page.
Competitors:
https://quillmarsh.example/
https://dorvinpalms.example/
https://www.kelbrookhomes.example/nevada
http://www.tpw-hoa.example/

Target Market(s)

homeowners

Industry/Entity Type

Real Estate

Coding

Coded - Design and coding required

Number of Pages Required

5+ page

Font styles to use
Serif

Colors
0292cd
33a6d7
e667a6
e34297

Requirements
Must have
• login to pay
• services page
• contact us
• order resale package
Nice to have
• page why an HOA would contract us

```html
<!DOCTYPE html>
<html lang="en">
<head>
<meta charset="utf-8">
<title>TEBSIRK HOA</title>
<link href="https://fonts.googleapis.com/css2?family=Oswald:wght@500;600&family=Raleway:ital,wght@0,400;0,500;0,600;0,700;1,500&display=swap" rel="stylesheet">
<style>
:root{
  --blue:#0292cd;
  --blue-soft:#33a6d7;
  --pink:#e34297;
  --pink-soft:#e667a6;
  --ink:#1d1d1d;
  --muted:#555;
  --white:#fff;
  --black:#0a0a0a;
}
*{box-sizing:border-box;margin:0;padding:0}
html,body{width:1200px;height:3490px;overflow:hidden}
body{position:relative;font-family:"Raleway",sans-serif;color:var(--ink);background:var(--white)}
.abs{position:absolute}
.topbar{left:0;top:0;width:1200px;height:41px;background:var(--blue)}
.dot{position:absolute;width:28px;height:28px;border-radius:50%;background:var(--blue-soft)}
.dot.pink{background:var(--pink)}
.topbar .info{position:absolute;top:12px;color:var(--white);font-size:15px;font-weight:500}
.header{left:0;top:41px;width:1200px;height:89px;background:var(--white)}
.brand{font-weight:600;color:var(--blue);letter-spacing:.5px}
.header .brand{position:absolute;left:77px;top:28px;font-size:28px}
.nav{position:absolute;right:66px;top:38px;display:flex;gap:25px;font-size:14.5px;font-weight:600;color:#222}
.nav .active{color:var(--pink)}
.hero{left:0;top:130px;width:1200px;height:547px;background:linear-gradient(90deg,#f2f2f2 0%,#e9e7e4 45%,#d8d2c8 75%,#efefef 100%)}
.hero h1{position:absolute;left:78px;top:148px;font-family:"Oswald",sans-serif;font-weight:600;font-size:51px;line-height:58px;color:#111;letter-spacing:-.5px}
.hero h1 span{color:var(--blue)}
.hero p{position:absolute;left:78px;top:272px;width:480px;font-size:15px;line-height:27px;color:#333}
.btn{position:absolute;display:flex;align-items:center;justify-content:center;font-weight:700;font-size:19px;color:var(--white);background:var(--pink)}
.btn.ghost{background:transparent;border:2px solid var(--pink);color:var(--pink)}
.arrow-c{position:absolute;width:48px;height:48px;border-radius:50%;border:1.5px solid #666}
.band{left:0;top:677px;width:1200px;height:364px;background:var(--blue)}
.sec-title{position:absolute;left:0;width:1200px;text-align:center;font-weight:600;font-size:44px}
.sec-sub{position:absolute;left:0;width:1200px;text-align:center;font-size:15.5px;color:var(--white)}
.rule{position:absolute;left:580px;width:40px;height:4px;background:var(--pink)}
.card{left:77px;top:844px;width:1046px;height:395px;background:var(--white);box-shadow:0 2px 8px rgba(0,0,0,.12)}
.svc-img{position:absolute;top:20px;width:492px;height:260px}
.svc-title{position:absolute;top:305px;font-size:22px;font-weight:600;line-height:29px;color:#222}
.about p{position:absolute;left:282px;width:636px;text-align:center;font-size:13.5px;line-height:27px;color:var(--muted)}
.testi{left:0;top:1718px;width:1200px;height:447px;background:linear-gradient(180deg,#1b8fd0,#2a9ad6)}
.quote-card{left:214px;top:1874px;width:833px;height:187px;background:rgba(230,242,250,.93);border-radius:6px}
.avatar{left:156px;top:1908px;width:116px;height:116px;border-radius:50%;border:4px solid var(--pink);background:linear-gradient(160deg,#8fb4d4,#3a4c66)}
.offer li{position:absolute;left:624px;list-style:none;font-size:14px;line-height:27px;color:#444;padding-left:22px;width:450px}
.offer li svg{position:absolute;left:0;top:7px}
.news{left:0;top:2796px;width:1200px;height:302px;background:linear-gradient(180deg,#1a7fc2,#2595d3)}
.footer{left:0;top:3098px;width:1200px;height:328px;background:var(--black)}
.f-title{position:absolute;top:3135px;font-size:19px;font-weight:700;color:var(--blue)}
.f-icon{position:absolute;width:46px;height:46px;border-radius:50%;border:2px solid var(--pink);display:flex;align-items:center;justify-content:center}
.f-text{position:absolute;left:497px;font-size:15px;line-height:25px;color:#ddd}
.copy{left:0;top:3426px;width:1200px;height:64px;background:var(--blue);color:var(--white);font-size:15px;text-align:center;line-height:64px}
</style>
</head>
<body>

<div class="abs topbar">
  <span class="dot pink" style="left:78px;top:6px" aria-label="Social link"></span>
  <span class="dot" style="left:113px;top:6px" aria-label="Social link"></span>
  <span class="dot" style="left:148px;top:6px" aria-label="Social link"></span>
  <span class="dot" style="left:183px;top:6px" aria-label="Social link"></span>
  <span class="info" style="left:764px">
    <svg width="16" height="16" viewBox="0 0 24 24" style="vertical-align:-3px;margin-right:6px"><path fill="#e34297" d="M6.6 10.8a15 15 0 0 0 6.6 6.6l2.2-2.2a1 1 0 0 1 1-.25 11.4 11.4 0 0 0 3.6.6 1 1 0 0 1 1 1V20a1 1 0 0 1-1 1A17 17 0 0 1 3 4a1 1 0 0 1 1-1h3.5a1 1 0 0 1 1 1c0 1.25.2 2.45.6 3.6a1 1 0 0 1-.25 1z"/></svg>555 014 2290</span>
  <span class="info" style="left:934px;font-weight:400;opacity:.9">
    <svg width="14" height="14" viewBox="0 0 24 24" style="vertical-align:-2px;margin-right:4px"><circle cx="10" cy="10" r="6.5" fill="none" stroke="#fff" stroke-width="3"/><path d="M15 15l6 6" stroke="#fff" stroke-width="3"/></svg>Search</span>
  <span class="info" style="left:1048px;font-weight:400;opacity:.9">
    <svg width="14" height="14" viewBox="0 0 24 24" style="vertical-align:-2px;margin-right:5px"><circle cx="12" cy="7" r="5" fill="#fff"/><path d="M3 22c0-6 4-9 9-9s9 3 9 9z" fill="#fff"/></svg>Login</span>
</div>

<header class="abs header">
  <div class="brand">TEBSIRK HOA</div>
  <nav class="nav">
    <span class="active">HOME</span><span>SERVICES</span><span>ORDER RESALE PACKAGE</span><span>WHY HOA CONTRACT US</span><span>CONTACT US</span>
  </nav>
</header>

<section class="abs hero">
  <div class="abs" role="img" aria-label="Photo of a smiling family of four standing in a bright living room by an open door" style="left:420px;top:0;width:780px;height:547px;background:linear-gradient(100deg,rgba(255,255,255,0) 0%,#d9cfc2 35%,#b8a690 60%,#e6e6e6 85%,#f7f7f7 100%)"></div>
  <h1><span>HOMEOWNER</span> ASSOCIATION<br>MANAGEMENT</h1>
  <p>Lorem Ipsum is simply dummy text of the printing and typesetting industry.&nbsp; Ipsum has been the industry's standard</p>
  <div class="btn" style="left:77px;top:342px;width:160px;height:53px">CONTACT US</div>
  <div class="btn ghost" style="left:246px;top:342px;width:106px;height:53px">LOGIN</div>
  <div class="arrow-c" style="left:13px;top:248px"><svg width="46" height="46" viewBox="0 0 46 46"><path d="M26 15l-8 8 8 8" fill="none" stroke="#555" stroke-width="1.5"/></svg></div>
  <div class="arrow-c" style="left:1139px;top:248px"><svg width="46" height="46" viewBox="0 0 46 46"><path d="M20 15l8 8-8 8" fill="none" stroke="#555" stroke-width="1.5"/></svg></div>
</section>

<section class="abs band"></section>
<h2 class="sec-title" style="top:721px;color:var(--white)">HOA Provide Best Services</h2>
<p class="sec-sub" style="top:781px">Lorem Ipsum is simply dummy text of the printing and typesetting industry type text.</p>

<div class="abs card">
  <div class="svc-img" role="img" aria-label="Photo of a hand holding a small model house" style="left:20px;background:radial-gradient(circle at 60% 45%,#6b6b6b 0%,#a8a29a 30%,#e4e1dc 70%)"></div>
  <div class="svc-img" role="img" aria-label="Photo of two colleagues working together at a laptop" style="left:534px;background:linear-gradient(120deg,#f0f0ee,#d3d1cc 55%,#eeeeec)"></div>
  <h3 class="svc-title" style="left:21px">Association Management Services</h3>
  <h3 class="svc-title" style="left:534px">Tebsirk Manages Communities<br>Throughout Southern Nevada</h3>
  <svg class="abs" style="left:475px;top:306px" width="36" height="36" viewBox="0 0 36 36"><circle cx="18" cy="18" r="15.5" fill="none" stroke="#0292cd" stroke-width="3"/><path d="M9 18h16M19 12l6 6-6 6" fill="none" stroke="#0292cd" stroke-width="3"/></svg>
  <svg class="abs" style="left:990px;top:306px" width="36" height="36" viewBox="0 0 36 36"><circle cx="18" cy="18" r="15.5" fill="none" stroke="#0292cd" stroke-width="3"/><path d="M9 18h16M19 12l6 6-6 6" fill="none" stroke="#0292cd" stroke-width="3"/></svg>
</div>

<section class="about">
  <h2 class="sec-title" style="top:1300px;color:var(--blue)">About Tebsirk Hoa</h2>
  <span class="rule" style="top:1359px"></span>
  <p style="top:1397px">Lorem Ipsum is simply dummy text of the printing and typesetting industry. Lorem Ipsum has been the industry's standard dummy text ever since an unknown</p>
  <p style="top:1467px">Lorem Ipsum is simply dummy text of the printing and typesetting industry. Lorem Ipsum has been the industry's standard dummy text ever since the 1500s, when an unknown printer took a galley of type and scrambled it to make a type specimen book. printer took a galley of type and scrambled it to make a type specimen book.</p>
  <div class="btn" style="left:511px;top:1602px;width:177px;height:51px">LEARN MORE</div>
</section>

<section class="abs testi" role="img" aria-label="Blue tinted photo of a modern house exterior"></section>
<h2 class="sec-title" style="top:1774px;color:var(--white)">What Our Client Say</h2>
<span class="rule" style="top:1835px"></span>
<div class="abs quote-card">
  <p class="abs" style="left:88px;top:46px;width:720px;font-style:italic;font-weight:500;font-size:15.5px;line-height:27px;color:#222">" Lorem Ipsum is simply dummy text of the printing and typesetting industry. Lorem Ipsum has been the industry's standard dummy text ever since the 1500s, when an unknown printer took a galley of type and scrambled it to make a type specimen book. "</p>
  <span class="abs" style="right:30px;top:146px;font-weight:700;font-size:16px;color:var(--pink)"><span style="display:inline-block;width:18px;height:3px;background:var(--pink);vertical-align:5px;margin-right:9px"></span>CLIENT NAME</span>
</div>
<div class="abs avatar" role="img" aria-label="Portrait photo of a client"></div>
<svg class="abs" style="left:556px;top:2095px" width="86" height="18" viewBox="0 0 86 18">
  <circle cx="9" cy="9" r="6" fill="none" stroke="#fff" stroke-width="1.5"/>
  <circle cx="31" cy="9" r="6" fill="none" stroke="#fff" stroke-width="1.5"/>
  <circle cx="53" cy="9" r="6" fill="none" stroke="#fff" stroke-width="1.5"/>
  <circle cx="77" cy="9" r="8" fill="#fff"/>
</svg>

<section class="offer">
  <div class="abs" role="img" aria-label="Photo of a hand holding a smartphone showing the portal login screen" style="left:80px;top:2220px;width:490px;height:576px;background:linear-gradient(160deg,#f4f4f4 0%,#e8e8e8 40%,#f0d8c8 70%,#e9c3ad 100%)"></div>
  <h2 class="abs" style="left:610px;top:2220px;font-size:44px;font-weight:600;color:var(--blue)">What We Offer</h2>
  <span class="abs" style="left:616px;top:2280px;width:40px;height:4px;background:var(--pink)"></span>
  <ul>
    <li style="top:2318px"><svg width="15" height="15" viewBox="0 0 16 16"><circle cx="8" cy="8" r="6.5" fill="none" stroke="#0292cd" stroke-width="2"/><path d="M5 8l2.2 2.2L11 6" fill="none" stroke="#0292cd" stroke-width="2"/></svg>Accessible, licensed Association Managers</li>
    <li style="top:2355px"><svg width="15" height="15" viewBox="0 0 16 16"><circle cx="8" cy="8" r="6.5" fill="none" stroke="#0292cd" stroke-width="2"/><path d="M5 8l2.2 2.2L11 6" fill="none" stroke="#0292cd" stroke-width="2"/></svg>24 hour Web site access: online account information</li>
    <li style="top:2391px"><svg width="15" height="15" viewBox="0 0 16 16"><circle cx="8" cy="8" r="6.5" fill="none" stroke="#0292cd" stroke-width="2"/><path d="M5 8l2.2 2.2L11 6" fill="none" stroke="#0292cd" stroke-width="2"/></svg>24 hour emergency service</li>
    <li style="top:2428px"><svg width="15" height="15" viewBox="0 0 16 16"><circle cx="8" cy="8" r="6.5" fill="none" stroke="#0292cd" stroke-width="2"/><path d="M5 8l2.2 2.2L11 6" fill="none" stroke="#0292cd" stroke-width="2"/></svg>Provide monthly financial reports to the Board of Directors</li>
    <li style="top:2470px"><svg width="15" height="15" viewBox="0 0 16 16"><circle cx="8" cy="8" r="6.5" fill="none" stroke="#0292cd" stroke-width="2"/><path d="M5 8l2.2 2.2L11 6" fill="none" stroke="#0292cd" stroke-width="2"/></svg>Read, study and understand all governing documents of the Association. Correspond with members in violation of the CC&amp;Rs, By-laws, Rules &amp; Regulations and report the status of all noncompliance to the Board of Directors in a timely manner.</li>
    <li style="top:2596px"><svg width="15" height="15" viewBox="0 0 16 16"><circle cx="8" cy="8" r="6.5" fill="none" stroke="#0292cd" stroke-width="2"/><path d="M5 8l2.2 2.2L11 6" fill="none" stroke="#0292cd" stroke-width="2"/></svg>Act as the custodian of the corporate records. Coordinate preparing annual tax returns for the Association.</li>
  </ul>
  <div class="btn" style="left:616px;top:2673px;width:177px;height:51px">LEARN MORE</div>
</section>

<section class="abs news" role="img" aria-label="Blue tinted photo of office building facades"></section>
<h2 class="sec-title" style="top:2858px;color:var(--white)">Newsletter Subscription</h2>
<span class="rule" style="top:2918px"></span>
<p class="sec-sub" style="top:2943px;font-style:italic;font-weight:500;font-size:16px">Would you like to Receive our Exclusive News and update for sign up Our Newsletter !</p>
<div class="abs" style="left:309px;top:2981px;width:417px;height:52px;background:var(--white);border-radius:3px;font-size:13px;color:#666;padding:17px 16px">Enter Email *</div>
<div class="btn" style="left:735px;top:2981px;width:155px;height:52px;border-radius:2px">SUBSCRIBE</div>

<footer class="abs footer"></footer>
<div class="abs brand" style="left:77px;top:3133px;font-size:28px">TEBSIRK HOA</div>
<p class="abs" style="left:79px;top:3183px;width:310px;font-size:13.5px;line-height:27px;color:#ddd">Lorem Ipsum is simply dummy text of the printing and typesetting industry. Lorem Ipsum has been the industry's standard dummy text ever since an unknown</p>
<span class="abs" style="left:77px;top:3301px;width:40px;height:40px;border-radius:50%;background:var(--pink)" aria-label="Social link"></span>
<span class="abs" style="left:124px;top:3301px;width:40px;height:40px;border-radius:50%;background:#2b2b2b" aria-label="Social link"></span>
<span class="abs" style="left:171px;top:3301px;width:40px;height:40px;border-radius:50%;background:#2b2b2b" aria-label="Social link"></span>
<span class="abs" style="left:217px;top:3301px;width:40px;height:40px;border-radius:50%;background:#2b2b2b" aria-label="Social link"></span>

<h4 class="f-title" style="left:435px">CONTACT US</h4>
<span class="f-icon" style="left:433px;top:3189px"><svg width="18" height="22" viewBox="0 0 18 22"><path d="M9 1a7 7 0 0 0-7 7c0 5 7 13 7 13s7-8 7-13a7 7 0 0 0-7-7z" fill="none" stroke="#e34297" stroke-width="2"/><circle cx="9" cy="8" r="2.5" fill="#e34297"/></svg></span>
<p class="f-text" style="top:3188px;width:260px">101 - Address city location, Area, Pincode, Zip...</p>
<span class="f-icon" style="left:433px;top:3252px"><svg width="18" height="18" viewBox="0 0 24 24"><path fill="#e34297" d="M6.6 10.8a15 15 0 0 0 6.6 6.6l2.2-2.2a1 1 0 0 1 1-.25 11.4 11.4 0 0 0 3.6.6 1 1 0 0 1 1 1V20a1 1 0 0 1-1 1A17 17 0 0 1 3 4a1 1 0 0 1 1-1h3.5a1 1 0 0 1 1 1c0 1.25.2 2.45.6 3.6a1 1 0 0 1-.25 1z"/></svg></span>
<p class="f-text" style="top:3263px">555 014 2290</p>
<span class="f-icon" style="left:433px;top:3312px"><svg width="20" height="16" viewBox="0 0 20 16"><rect x="1" y="1" width="18" height="14" rx="2" fill="#e34297"/><path d="M1 2l9 7 9-7" fill="none" stroke="#0a0a0a" stroke-width="1.5"/></svg></span>
<p class="f-text" style="top:3323px">info@TebsirkHOA.com</p>

<h4 class="f-title" style="left:791px">LOCATION MAP</h4>
<div class="abs" role="img" aria-label="Grey world map illustration with a location pin" style="left:791px;top:3182px;width:312px;height:203px;background:radial-gradient(ellipse at 50% 50%,#9a9a9a 0%,#5a5a5a 55%,#0a0a0a 75%)"></div>

<div class="abs copy">©TEBSIRK HOA - 2019 All rights reserved.</div>

</body>
</html>
```